Corvane Paintless Dent Removal

Our company works on vehicles removing dents using a highly skilled trade which the metal is massaged out with special tools without disturbing the original paint, hence paintless dent removal. Besides keeping the paint and metal original its also very environmentally friendly since no paint or toxic fillers are used. Also we we are one of the most experienced companies in the business with 25 years

Target Market(s)

Retail Automobile consumers, Auto Dealerships and Auto Body Shops

Industry/Entity Type

Auto Repair

Contact Information for Business Card

Dale Hollister
PO Box 518 Brookmere, NY 11962
631-555-0148
corvanepdr@mailbox-example.com
website corvanepdr.example
youtube corvane paintless dent removal
25 years of experience removing Dents, Dings and Hail Damage

Font styles to use
Serif
Sans Serif

Colors

Designer to choose colors to be used in the design.

Requirements
Must have
• I do like things that are simple but classy and somewhat bold, also I like my logo so that should be somewhat important

```html
<!DOCTYPE html>
<html lang="en">
<head>
<meta charset="utf-8">
<title>Corvane Paintless Dent Removal – Business Card</title>
<link rel="stylesheet" href="https://fonts.googleapis.com/css2?family=Roboto+Condensed:wght@400;700&family=Roboto:wght@400;700&display=swap">
<style>
  :root {
    --navy: #13305c;
    --navy-deep: #0f2a52;
    --green: #7dc424;
    --gold: #c99a1e;
    --paper: #ffffff;
    --ink-soft: #5a5f66;
    --rule: #8a8f96;
    --stage: #e9e7e3;
  }
  * { margin: 0; padding: 0; box-sizing: border-box; }
  html, body { width: 1200px; height: 886px; overflow: hidden; }
  body {
    background: var(--stage);
    font-family: "Roboto", Arial, sans-serif;
    display: flex; flex-direction: column; align-items: center; justify-content: center;
    gap: 46px;
  }
  .card {
    width: 700px; height: 400px; position: relative;
    box-shadow: 0 6px 22px rgba(0,0,0,.18);
  }
  .card--front { background: var(--paper); }
  .card--back { background: var(--navy-deep); display: flex; align-items: center; justify-content: center; }

  .brand { display: flex; align-items: center; gap: 14px; }
  .brand__dot { width: 26px; height: 26px; border-radius: 50%; background: var(--green); flex: none; }
  .brand__name {
    font-family: "Roboto", Arial, sans-serif; font-weight: 700;
    font-size: 30px; letter-spacing: .5px; color: var(--navy); text-transform: uppercase;
    line-height: 1.15; max-width: 330px;
  }
  .card--back .brand__name { color: #ffffff; }

  .card--front .brand { position: absolute; left: 70px; top: 78px; }

  .holder {
    position: absolute; left: 70px; bottom: 52px; width: 250px;
    border-top: 1.5px solid var(--rule); padding-top: 16px;
  }
  .holder__name {
    font-family: "Roboto Condensed", Arial, sans-serif; font-weight: 700;
    font-size: 25px; color: var(--navy); text-transform: uppercase; letter-spacing: .3px;
  }
  .holder__address { font-family: "Roboto Condensed", Arial, sans-serif; font-size: 17px; color: var(--ink-soft); line-height: 1.45; margin-top: 4px; }

  .contact {
    position: absolute; right: 48px; bottom: 52px; width: 320px;
    border-top: 1.5px solid var(--rule); padding-top: 16px;
    list-style: none; text-align: right;
  }
  .contact__item {
    font-family: "Roboto Condensed", Arial, sans-serif; font-size: 16px; color: var(--ink-soft);
    display: flex; justify-content: flex-end; align-items: center; gap: 10px; line-height: 1.7;
  }
  .contact__icon { width: 14px; height: 14px; flex: none; }

  .website {
    position: absolute; bottom: 30px; left: 0; right: 0; text-align: center;
    font-size: 15px; letter-spacing: 7px; color: #dfe6f0;
  }
  .badge { position: absolute; right: 40px; bottom: 28px; width: 66px; height: 66px; }
</style>
</head>
<body>
  <section class="card card--front">
    <div class="brand">
      <span class="brand__dot"></span>
      <span class="brand__name">Corvane Paintless Dent Removal</span>
    </div>

    <div class="holder">
      <p class="holder__name">Dale Hollister</p>
      <p class="holder__address">PO Box 518<br>Brookmere, NY 11962</p>
    </div>

    <ul class="contact">
      <li class="contact__item">631-555-0148
        <svg class="contact__icon" viewBox="0 0 16 16"><path fill="#13305c" d="M3 1h3l1.5 4-2 1.2a9 9 0 0 0 4.3 4.3L11 8.5l4 1.5v3a2 2 0 0 1-2 2A12 12 0 0 1 1 3a2 2 0 0 1 2-2z"/></svg>
      </li>
      <li class="contact__item">corvanepdr@mailbox-example.com
        <svg class="contact__icon" viewBox="0 0 16 16"><rect x="1" y="3" width="14" height="10" rx="1.5" fill="#13305c"/><path d="M2 4l6 5 6-5" stroke="#fff" stroke-width="1.3" fill="none"/></svg>
      </li>
      <li class="contact__item">corvane paintless dent removal
        <svg class="contact__icon" viewBox="0 0 16 16"><rect x="1" y="1" width="14" height="14" rx="2" fill="#13305c"/></svg>
      </li>
    </ul>
  </section>

  <section class="card card--back">
    <div class="brand">
      <span class="brand__dot"></span>
      <span class="brand__name">Corvane Paintless Dent Removal</span>
    </div>
    <p class="website">www.corvanepdr.example</p>
    <svg class="badge" viewBox="0 0 66 66" role="img" aria-label="25 years of experience seal">
      <circle cx="33" cy="33" r="32" fill="var(--gold)"/>
      <circle cx="33" cy="33" r="22" fill="#1a1a1a"/>
    </svg>
  </section>
</body>
</html>
```